Modern design company business card design

We are a design oriented construction firm. The owner is an architect and licensed General Contractor and accomplished furniture designer. We do new home construction and large scale remodeling and office design. We would like a design for our new business cards that is clean and modern, but relatable. We like the bright green color of our logo mixed with different shades of grey. We're also open to reinterpreting the logo.

Target Market(s)

Potential design clients,
Construction clients

Industry/Entity Type

Architecture

Contact Information for Business Card

Tall Maple Design | Build Inc. (optional with logo, Inc. optional)Jeffrey MorganOwner (optional)317.555.0148 cell317.431.8056 officejmorgan@greensquareinc.comwww.greensquareinc.com

Font styles to use
Sans Serif
Other font styles liked:
• Avenir

Requirements
Nice to have
• I like designs that have some continuity between the front and back, i.e. similar layouts or graphic elements that wrap around the card. I tend to prefer horizontal over vertical, but that's not a have to. I also tend to prefer white or recycled paper.

```html
<!DOCTYPE html>
<html lang="en">
<head>
<meta charset="utf-8">
<title>Tall Maple Design | Build — Business Card</title>
<link rel="stylesheet" href="https://fonts.googleapis.com/css2?family=Mulish:wght@400;600;800&display=swap">
<style>
  :root {
    --green: #5cb531;
    --green-light: #9fd45a;
    --ink: #6b6b6b;
    --ink-soft: #8a8a8a;
    --paper: #ffffff;
    --slate-top: #8c8f93;
    --slate-bottom: #3a3c3f;
    --backdrop: #e9e9e7;
  }
  * { box-sizing: border-box; margin: 0; padding: 0; }
  html, body {
    width: 1200px; height: 913px; overflow: hidden;
    background: var(--backdrop);
    font-family: "Mulish", "Avenir", sans-serif;
  }
  .sheet {
    width: 1200px; height: 913px;
    display: flex; align-items: center; justify-content: center; gap: 60px;
  }
  .card {
    position: relative;
    width: 525px; height: 300px;
    box-shadow: 0 6px 18px rgba(0,0,0,.18);
    overflow: hidden;
  }

  /* Front */
  .card--front { background: var(--paper); }
  .card__tab {
    position: absolute; top: 0; right: 0;
    width: 36px; height: 22px; background: var(--green-light);
  }
  .contact {
    position: absolute; top: 20px; right: 28px;
    text-align: right; color: var(--ink-soft);
    font-size: 13px; line-height: 18px;
  }
  .contact__name {
    font-weight: 800; font-size: 18px; letter-spacing: .5px;
    color: var(--ink); text-transform: uppercase; line-height: 24px;
  }
  .contact__role {
    color: var(--green); font-size: 12px; font-weight: 600;
    letter-spacing: 1px; text-transform: uppercase;
  }
  .contact__row {
    display: flex; justify-content: flex-end; align-items: center; gap: 6px;
    white-space: nowrap;
  }
  .contact__row svg { width: 11px; height: 11px; flex: none; }
  .contact__rule {
    position: absolute; top: 160px; right: 28px; left: 28px;
    height: 1px; background: var(--green);
  }

  .brand {
    position: absolute; display: flex; align-items: center; gap: 12px;
    white-space: nowrap;
  }
  .brand__dot {
    width: 14px; height: 14px; border-radius: 50%; flex: none;
    background: var(--green);
  }
  .brand__name {
    font-weight: 600; letter-spacing: 2px; text-transform: uppercase;
  }
  .card--front .brand { left: 28px; bottom: 36px; }
  .card--front .brand__name { color: var(--ink); font-size: 18px; }

  /* Back */
  .card--back {
    background: linear-gradient(170deg, var(--slate-top), var(--slate-bottom));
  }
  .card--back .brand { left: 50%; top: 50%; transform: translate(-50%, -50%); }
  .card--back .brand__name { color: #ffffff; font-size: 22px; }
</style>
</head>
<body>
<main class="sheet">
  <section class="card card--front" aria-label="Card front">
    <div class="card__tab"></div>
    <div class="contact">
      <p class="contact__name">Dennis Holloway</p>
      <p class="contact__role">Owner</p>
      <p class="contact__row">317.555.0172
        <svg viewBox="0 0 12 12" aria-hidden="true"><rect x="3" y="1" width="6" height="10" rx="1" fill="none" stroke="#5cb531" stroke-width="1.2"/></svg>
      </p>
      <p class="contact__row">317.555.0148
        <svg viewBox="0 0 12 12" aria-hidden="true"><path d="M3 1.5l2 2.5-1 1.2a6 6 0 0 0 2.8 2.8l1.2-1 2.5 2-1 1.5C5 10 2 7 1.5 2.5z" fill="#5cb531"/></svg>
      </p>
      <p class="contact__row">www.tallmapleinc.example
        <svg viewBox="0 0 12 12" aria-hidden="true"><circle cx="6" cy="6" r="4.8" fill="none" stroke="#5cb531" stroke-width="1.1"/><path d="M1.2 6h9.6M6 1.2c-2.2 2.6-2.2 7 0 9.6M6 1.2c2.2 2.6 2.2 7 0 9.6" fill="none" stroke="#5cb531" stroke-width=".9"/></svg>
      </p>
      <p class="contact__row">dholloway@tallmapleinc.example
        <svg viewBox="0 0 12 12" aria-hidden="true"><rect x="1" y="2.5" width="10" height="7" fill="none" stroke="#5cb531" stroke-width="1.1"/><path d="M1 2.5l5 4 5-4" fill="none" stroke="#5cb531" stroke-width="1.1"/></svg>
      </p>
    </div>
    <div class="contact__rule"></div>
    <div class="brand">
      <span class="brand__dot"></span>
      <p class="brand__name">Tall Maple Design | Build</p>
    </div>
  </section>

  <section class="card card--back" aria-label="Card back">
    <div class="brand">
      <span class="brand__dot"></span>
      <p class="brand__name">Tall Maple Design | Build</p>
    </div>
  </section>
</main>
</body>
</html>
```